Business Cards Design for the electrical wholesaler: clean bold dynamic :)

We need a business card design that would follow our latest brand guidelines. As an electrical wholesaler we want to bring a fresh look and feel into the industry. The design should be clean bold and dynamic. It should come alive with the renewed energy of our green colour. Our grey colour should keep things balanced and complement the notion of maturity and responsibility. We employ Lato as a corporate font however are not bound by this font and we’re open to interpretation here.

Target Market(s)

Electrical contractors

Industry/Entity Type

Business

Contact Information for Business Card

Logo
Name & Surname: Halyna Dorosh
Job Title: Director of Marketing
Email: halya.dorosh@quillmail.example
Cell phone: XXX.XXX.XXXX
Address: 20517 - 87 Ave. Edmonton, AB, Canada. T6K 4N8
Business Phone: 780.555.0184
Website: www.brovix.example

Font styles to use
Other font styles liked:
• Lato

Requirements
Must have
• Logo & website
Nice to have
• Brand elements - some of them you may find in the attached Brand Guidelines (e.g. three lines on the background signifying "W")

```html
<!DOCTYPE html>
<html lang="en">
<head>
<meta charset="utf-8">
<title>Brovix Electrical Wholesalers – Business Card</title>
<link rel="stylesheet" href="https://fonts.googleapis.com/css2?family=Lato:wght@400;700&display=swap">
<style>
  :root {
    --brand-green: #80bd3a;
    --brand-grey: #4b4b4d;
    --text-grey: #555557;
    --rule-grey: #8a8a8a;
    --paper: #f7f7f5;
    --backdrop: #d3d3d3;
  }
  * { margin: 0; padding: 0; box-sizing: border-box; }
  html, body { width: 1200px; height: 960px; overflow: hidden; }
  body {
    position: relative;
    background: var(--backdrop);
    font-family: "Lato", Arial, sans-serif;
    color: var(--text-grey);
  }
  .card { position: absolute; }

  /* Front side */
  .card-front {
    left: 320px; top: 95px; width: 605px; height: 360px;
    background: var(--brand-green);
  }
  .front-identity {
    position: absolute; right: 38px; bottom: 38px;
    text-align: right; color: var(--brand-grey);
  }
  .front-wordmark {
    font-size: 86px; font-weight: 400; line-height: 0.9; letter-spacing: -1px;
  }
  .front-tagline {
    margin-top: 10px; font-size: 14px; font-weight: 700; letter-spacing: 1.6px;
  }
  .front-web {
    margin-top: 4px; font-size: 14px; letter-spacing: 2.2px;
  }

  /* Back side */
  .card-back {
    left: 320px; top: 492px; width: 600px; height: 343px;
    background: var(--paper);
  }
  .back-logo {
    position: absolute; left: 38px; top: 44px;
    display: flex; align-items: center; gap: 12px;
  }
  .logo-square {
    width: 42px; height: 42px; background: var(--brand-green);
  }
  .logo-text { color: var(--brand-grey); }
  .logo-name { font-size: 46px; font-weight: 400; line-height: 0.9; letter-spacing: -0.5px; }
  .logo-tagline { font-size: 9px; font-weight: 700; letter-spacing: 1.2px; margin-top: 3px; }

  .holder {
    position: absolute; right: 35px; top: 172px; text-align: right;
  }
  .holder-name { color: var(--brand-green); font-size: 20px; font-weight: 700; line-height: 1.1; }
  .holder-title { font-size: 16px; line-height: 1.2; letter-spacing: 0.3px; }
  .accent-bar {
    position: absolute; right: 0; top: 175px; width: 14px; height: 38px;
    background: var(--brand-green);
  }
  .divider {
    position: absolute; left: 40px; right: 35px; top: 225px;
    border-top: 1px solid var(--rule-grey);
  }
  .contacts {
    position: absolute; left: 38px; top: 238px; list-style: none;
    font-size: 14.5px; line-height: 19px;
  }
  .contacts li { display: flex; align-items: center; gap: 8px; }
  .contacts svg { width: 14px; height: 14px; fill: var(--brand-green); flex: none; }
  .address {
    position: absolute; right: 34px; top: 258px; text-align: right;
    font-size: 14.5px; line-height: 19px; font-style: normal;
  }
</style>
</head>
<body>

<section class="card card-front" aria-label="Card front">
  <div class="front-identity">
    <div class="front-wordmark">brovix</div>
    <div class="front-tagline">ELECTRICAL WHOLESALERS</div>
    <div class="front-web">www.brovix.example</div>
  </div>
</section>

<section class="card card-back" aria-label="Card back">
  <div class="back-logo">
    <span class="logo-square"></span>
    <div class="logo-text">
      <div class="logo-name">brovix</div>
      <div class="logo-tagline">ELECTRICAL WHOLESALERS</div>
    </div>
  </div>

  <div class="holder">
    <div class="holder-name">HALYNA DOROSH</div>
    <div class="holder-title">CEO/FOUNDER</div>
  </div>
  <span class="accent-bar"></span>
  <div class="divider"></div>

  <ul class="contacts">
    <li>
      <svg viewBox="0 0 16 16" aria-hidden="true"><path d="M3.6 1.2l2.3 2.6-1.3 1.9c.9 2 2.5 3.6 4.6 4.6l1.9-1.3 2.6 2.3-1.2 2.5C7 13.6 2.4 9 1.2 3z"/></svg>
      780.555.0184
    </li>
    <li>
      <svg viewBox="0 0 16 16" aria-hidden="true"><path d="M4.5 1h7v14h-7zM6 3v9h4V3zm1.3 10v1h1.4v-1z" fill-rule="evenodd"/></svg>
      780.555.0191
    </li>
    <li>
      <svg viewBox="0 0 16 16" aria-hidden="true"><path d="M4 1h7l1 1v3H4zM1 6h14v6h-2v3H3v-3H1zm4 5v2.5h6V11z" fill-rule="evenodd"/></svg>
      780.555.0127
    </li>
    <li>
      <svg viewBox="0 0 16 16" aria-hidden="true"><path d="M1 3.5h14v9H1zm1.5 1.2L8 8.6l5.5-3.9z" fill-rule="evenodd"/></svg>
      halya.dorosh@quillmail.example
    </li>
  </ul>

  <address class="address">
    20517 - 87 Ave.<br>
    Edmonton, AB, Canada. T6K 4N8<br>
    www.brovix.example
  </address>
</section>

</body>
</html>
```